Fire Risk Assessment App needs a sleek UI design

I need a sleek, modern but professional design for my 5 page Fire Risk Assessment App. Include gradient background, fire themed colours including reds, yellows, light orange and a touch of black. Design must ooze simplicity and professionalism. This is for the UK market. See attached images and word doc for more information.

Target Market(s)

General public and business owners

Industry/Entity Type

Technology / Fire Safety

Colors
00AB8E
00BBA5
67D7C9
C6EFE9
E9F9F6
59FF00
82FF00
B8FF75
E3FFCB
F4FFEA
FFC000
F8CF3A
FAE287
FDF2CF
FEFAEE
F0912C
F2A743
F7CA91
FBE8D2
FDF5EE
EE7325
F08F49
F5BC92
FAE3D3
FDF4ED
EB3D1F
EC4F4E
F09395
F8D3D4
FCEDEE

```html
<!DOCTYPE html>
<html lang="en">
<head>
<meta charset="utf-8">
<title>Fire Risk Assessment App – Screens</title>
<link href="https://fonts.googleapis.com/css2?family=Montserrat:wght@400;500;600;700&display=swap" rel="stylesheet">
<style>
:root{
  --bg:#fbf6ea;
  --orange:#f2a743;
  --orange-soft:#f7ca91;
  --red:#eb3d1f;
  --ink:#1b1b1b;
  --muted:#666;
  --line:#e6dcd0;
  --white:#ffffff;
}
*{box-sizing:border-box;margin:0;padding:0}
html,body{width:1200px;height:1048px;overflow:hidden}
body{background:var(--bg);font-family:"Montserrat",sans-serif;color:var(--ink);position:relative}
.screen{position:absolute;top:104px;width:360px;height:840px;border-radius:30px;overflow:hidden;
  background:linear-gradient(160deg,#fdf0e6 0%,#fdf8dc 45%,#fbe1df 80%,#f7e7e4 100%);
  box-shadow:0 10px 30px rgba(120,90,40,.15)}
.screen--intro{left:30px}
.screen--dashboard{left:420px}
.screen--support{left:810px}
.abs{position:absolute}
/* intro */
.intro-title{top:44px;left:0;width:100%;text-align:center;font-size:18px;line-height:27px;font-weight:500}
.intro-title b{font-weight:700}
.form-preview{top:106px;left:40px;width:280px;height:300px;border-radius:10px;
  background:linear-gradient(170deg,#ffffff 0%,#fdf6ee 70%,#fbeee0 100%);border:1px solid var(--line)}
.intro-line{left:0;width:100%;text-align:center;font-size:14px;font-weight:500}
.intro-line b{font-weight:700}
.accent-rule{left:160px;width:40px;height:2px;background:var(--orange)}
.account-btn{left:72px;width:218px;height:80px;background:var(--white);border-radius:6px;box-shadow:0 2px 8px rgba(0,0,0,.06);
  display:flex;flex-direction:column;align-items:center;justify-content:center;gap:6px;font-size:14px;font-weight:500}
/* headers */
.screen-head{display:flex;align-items:center;gap:12px;font-size:21px;font-weight:600;letter-spacing:.5px}
.head-badge{width:44px;height:44px;border-radius:50%;background:var(--orange);display:flex;align-items:center;justify-content:center}
/* dashboard */
.circle-btn{width:80px;height:80px;border-radius:50%;background:var(--white);box-shadow:0 3px 10px rgba(0,0,0,.08);display:flex;align-items:center;justify-content:center}
.node-label{font-size:13px;font-weight:700;text-align:center}
.status-pill{left:12px;width:182px;height:36px;background:var(--white);border-radius:8px;box-shadow:0 2px 8px rgba(0,0,0,.08);
  display:flex;align-items:center;justify-content:space-between;padding:0 14px 0 24px;font-size:12px;font-weight:700;letter-spacing:.5px}
.job-list{left:12px;list-style:none;font-size:11.5px;font-weight:500;letter-spacing:.3px}
.job-list li{display:flex;align-items:center;gap:10px;height:30px}
.job-list li::before{content:"";width:8px;height:8px;border:2px solid var(--ink);border-radius:50%}
.nav-bar{left:0;bottom:0;width:100%;height:48px;background:var(--white);display:flex;justify-content:space-around;align-items:center}
.nav-item{width:48px;height:48px;display:flex;align-items:center;justify-content:center;border-radius:50%}
.nav-item--active{background:var(--orange)}
/* support */
.reply-box{top:136px;left:16px;width:326px;height:222px;background:var(--white);border-radius:6px;box-shadow:0 2px 8px rgba(0,0,0,.05);padding:14px;font-size:11px;color:#888}
.send-btn{top:372px;right:18px;width:92px;height:30px;background:var(--orange);color:#fff;font-size:14px;font-weight:600;display:flex;align-items:center;justify-content:center}
</style>
</head>
<body>

<!-- Intro screen -->
<section class="screen screen--intro">
  <h1 class="abs intro-title">The most <b>‘user friendly’</b> Fire Risk<br>Assessment App available.</h1>
  <div class="abs form-preview" role="img" aria-label="Preview of a fire risk assessment question card with quick tap answer buttons"></div>
  <p class="abs intro-line" style="top:438px">Quick tap <b>responses and voice activated</b> typing</p>
  <div class="abs accent-rule" style="top:462px"></div>
  <div class="abs account-btn" style="top:478px">
    <svg width="34" height="34" viewBox="0 0 34 34"><circle cx="14" cy="9" r="6" fill="none" stroke="var(--ink)" stroke-width="2"/><path d="M3 30 C3 20 25 20 25 30" fill="none" stroke="var(--ink)" stroke-width="2"/><circle cx="27" cy="26" r="6" fill="#3bb54a"/><path d="M27 22v8M23 26h8" stroke="#fff" stroke-width="2"/></svg>
    Create a Free account
  </div>
  <p class="abs intro-line" style="top:596px">Any <b>Responsible Person</b> can do it.</p>
  <div class="abs account-btn" style="top:638px">
    <svg width="34" height="34" viewBox="0 0 34 34"><circle cx="14" cy="9" r="6" fill="none" stroke="var(--ink)" stroke-width="2"/><path d="M3 30 C3 20 25 20 25 30" fill="none" stroke="var(--ink)" stroke-width="2"/><circle cx="27" cy="26" r="6" fill="#3b8fe0"/><rect x="24.5" y="25" width="5" height="4" fill="#fff"/><path d="M25.5 25v-1.5a1.5 1.5 0 0 1 3 0V25" stroke="#fff" fill="none"/></svg>
    Customer Log in
  </div>
  <p class="abs intro-line" style="top:752px;font-weight:600;font-size:14.5px">Created and research by British Firefighters</p>
</section>

<!-- Dashboard screen -->
<section class="screen screen--dashboard">
  <div class="abs screen-head" style="top:54px;left:106px">
    <span class="head-badge"><svg width="28" height="22" viewBox="0 0 28 22" fill="none" stroke="#fff" stroke-width="1.8"><path d="M3 19 A11 11 0 1 1 25 19"/><path d="M5 12l2 1M8 6l1.5 1.5M14 3v2M20 6l-1.5 1.5M23 12l-2 1"/><path d="M14 19 L17 10"/><circle cx="14" cy="19" r="1.5" fill="#fff"/></svg></span>
    DASHBOARD
  </div>
  <svg class="abs" style="top:150px;left:0" width="360" height="100"><path d="M180 40 L100 100 M180 40 L300 100" stroke="var(--line)" stroke-width="1.5"/></svg>
  <div class="abs circle-btn" style="top:116px;left:168px"><svg width="34" height="34" viewBox="0 0 34 34"><path d="M12 2h10v10h10v10H22v10H12V22H2V12h10z" fill="none" stroke="var(--red)" stroke-width="2" stroke-linejoin="round"/></svg></div>
  <p class="abs node-label" style="top:202px;left:0;width:100%">START FIRE RISK ASSESSMENT</p>
  <div class="abs circle-btn" style="top:220px;left:62px">
    <svg width="42" height="42" viewBox="0 0 42 42" fill="none" stroke="var(--ink)" stroke-width="1.4">
      <path d="M3 39h36"/>
      <rect x="5" y="16" width="12" height="23"/>
      <rect x="17" y="6" width="18" height="33"/>
      <path d="M22 2h8v4"/><path d="M22 6V2"/>
      <path d="M8 20h2M12 20h2M8 25h2M12 25h2M8 30h2M12 30h2"/>
      <path d="M21 11h3M28 11h3M21 16h3M28 16h3M21 21h3M28 21h3M21 26h3M28 26h3"/>
      <rect x="23" y="31" width="6" height="8"/>
    </svg>
  </div>
  <p class="abs node-label" style="top:306px;left:42px;width:120px">Commercial</p>
  <div class="abs circle-btn" style="top:220px;left:272px">
    <svg width="42" height="42" viewBox="0 0 42 42" fill="none" stroke="var(--ink)" stroke-width="1.4" stroke-linejoin="round">
      <path d="M2 39h38"/>
      <path d="M3 24 L13 14 L23 24"/><path d="M6 21v18h14V21"/>
      <rect x="10" y="30" width="5" height="9"/><rect x="9" y="23" width="4" height="4"/><rect x="15" y="23" width="3" height="4"/>
      <path d="M17 14 L28 3 L39 14"/><path d="M21 10v3M35 10v29H21"/>
      <rect x="25" y="15" width="3" height="4"/><rect x="31" y="15" width="3" height="4"/>
      <rect x="25" y="24" width="3" height="4"/><rect x="30" y="30" width="5" height="9"/>
      <path d="M31 5V2h3v6"/>
    </svg>
  </div>
  <p class="abs node-label" style="top:306px;left:252px;width:120px">Residential</p>

  <div class="abs status-pill" style="top:380px">COMPLETE<svg width="22" height="22" viewBox="0 0 22 22"><path d="M19 9.5A8 8 0 1 1 15 4" fill="none" stroke="var(--ink)" stroke-width="1.5"/><path d="M6 11l4 4 10-11" fill="none" stroke="var(--ink)" stroke-width="1.8"/></svg></div>
  <ul class="abs job-list" style="top:424px"><li>RAY'S BARBERSHOP</li></ul>
  <div class="abs status-pill" style="top:494px">IN PROGRESS<svg width="24" height="24" viewBox="0 0 24 24" fill="none" stroke="var(--ink)" stroke-width="1.5"><path d="M4 8a9 9 0 0 1 15-3M20 16a9 9 0 0 1-15 3"/><path d="M19 2v3h-3M5 22v-3h3"/><path d="M8 6h8M8 18h8M9 6c0 4 6 5 6 12M15 6c0 4-6 5-6 12"/></svg></div>
  <ul class="abs job-list" style="top:536px"><li>BROOK LANE SCHOOL</li><li>ELM COURT NURSING HOME</li></ul>
  <div class="abs status-pill" style="top:640px">PURCHASES<svg width="24" height="24" viewBox="0 0 24 24" fill="none" stroke="var(--ink)" stroke-width="1.4"><path d="M3 8h14l-1 13H4z M7 8V6a3 3 0 0 1 6 0v2"/><path d="M14 13l4-2 4 2v4c0 2-2 4-4 5-2-1-4-3-4-5z" fill="var(--white)"/><path d="M16 16l1.5 1.5 2.5-3"/></svg></div>
  <ul class="abs job-list" style="top:684px"><li>RESIDENTIAL FIRE RISK ASSESSMENT</li><li>COMMERCIAL FIRE RISK ASSESSMENT</li><li>COMMERCIAL FIRE RISK ASSESSMENT</li></ul>

  <nav class="abs nav-bar">
    <span class="nav-item nav-item--active"><svg width="30" height="22" viewBox="0 0 28 22" fill="none" stroke="#fff" stroke-width="1.6"><path d="M3 19 A11 11 0 1 1 25 19"/><path d="M5 12l2 1M8 6l1.5 1.5M14 3v2M20 6l-1.5 1.5M23 12l-2 1"/><path d="M14 19 L17 10"/></svg></span>
    <span class="nav-item"><svg width="26" height="28" viewBox="0 0 26 28" fill="none" stroke="var(--ink)" stroke-width="1.4"><path d="M3 2h15l5 5v19H3z"/><path d="M18 2v5h5"/><path d="M7 9h8M7 13h12M7 17h12M7 21h12"/><path d="M5 9h0M5 13h0"/></svg></span>
    <span class="nav-item"><svg width="30" height="28" viewBox="0 0 30 28" fill="none" stroke="var(--ink)" stroke-width="1.4"><circle cx="11" cy="6" r="2.5"/><circle cx="19" cy="6" r="2.5"/><circle cx="15" cy="11" r="2.5"/><path d="M7 13c0-2 8-2 8 0M15 13c0-2 8-2 8 0"/><path d="M2 10l2 7c1 4 5 7 10 8M28 10l-2 7c-1 4-5 7-10 8"/><path d="M4 17l4-1M26 17l-4-1"/></svg></span>
    <span class="nav-item"><svg width="36" height="26" viewBox="0 0 36 26" fill="none" stroke="var(--ink)" stroke-width="1.4"><path d="M2 2h20v22H2"/><path d="M2 2v22"/><circle cx="13" cy="6" r="2"/><path d="M12 9l-3 6 5 4-1 4M11 12l-4 1M12 10l4 3 3-1M9 15l-3 5"/><path d="M25 13h9M30 9l4 4-4 4"/></svg></span>
  </nav>
</section>

<!-- Technical support screen -->
<section class="screen screen--support">
  <div class="abs screen-head" style="top:52px;left:26px">
    <span class="head-badge"><svg width="26" height="26" viewBox="0 0 26 26" fill="none" stroke="#fff" stroke-width="1.6"><circle cx="12" cy="10" r="4.5"/><path d="M5 11a7 7 0 0 1 14 0v2h-2"/><path d="M4 24c1-5 15-5 16 0"/><path d="M19 2h5v3h-3l-2 1z"/></svg></span>
    TECHNICAL SUPPORT
  </div>
  <div class="abs reply-box">Type / record you response here
    <svg style="position:absolute;right:14px;top:14px" width="14" height="20" viewBox="0 0 14 20" fill="none" stroke="#333" stroke-width="1.5"><rect x="4" y="1" width="6" height="11" rx="3"/><path d="M1 9a6 6 0 0 0 12 0M7 15v4"/></svg>
  </div>
  <div class="abs send-btn">SEND</div>
  <nav class="abs nav-bar">
    <span class="nav-item"><svg width="30" height="22" viewBox="0 0 28 22" fill="none" stroke="var(--ink)" stroke-width="1.4"><path d="M3 19 A11 11 0 1 1 25 19"/><path d="M5 12l2 1M8 6l1.5 1.5M14 3v2M20 6l-1.5 1.5M23 12l-2 1"/><path d="M14 19 L17 10"/></svg></span>
    <span class="nav-item"><svg width="26" height="28" viewBox="0 0 26 28" fill="none" stroke="var(--ink)" stroke-width="1.4"><path d="M3 2h15l5 5v19H3z"/><path d="M18 2v5h5"/><path d="M7 9h8M7 13h12M7 17h12M7 21h12"/></svg></span>
    <span class="nav-item nav-item--active"><svg width="30" height="28" viewBox="0 0 30 28" fill="none" stroke="#fff" stroke-width="1.4"><circle cx="11" cy="6" r="2.5"/><circle cx="19" cy="6" r="2.5"/><circle cx="15" cy="11" r="2.5"/><path d="M7 13c0-2 8-2 8 0M15 13c0-2 8-2 8 0"/><path d="M2 10l2 7c1 4 5 7 10 8M28 10l-2 7c-1 4-5 7-10 8"/><path d="M4 17l4-1M26 17l-4-1"/></svg></span>
    <span class="nav-item"><svg width="36" height="26" viewBox="0 0 36 26" fill="none" stroke="var(--ink)" stroke-width="1.4"><path d="M2 2h20v22H2"/><path d="M2 2v22"/><circle cx="13" cy="6" r="2"/><path d="M12 9l-3 6 5 4-1 4M11 12l-4 1M12 10l4 3 3-1M9 15l-3 5"/><path d="M25 13h9M30 9l4 4-4 4"/></svg></span>
  </nav>
</section>

</body>
</html>
```